Refer a Friend A5 Flyer for Healthcare Staff

We need an A5 flyer that we can hand out to existing and new staff members promoting our Refer a friend Scheme. We need the leaflet to encourage staff to talk to their family and friends about joining our Healthcare Agency, which provides staff to local care related establishments. Using our logo and brand colours blue and green, as per our website, the final design will need to clearly convey the benefits and attractions of referring additional staff to the team. In addition is the promotion of our Chatterbook page, requesting staff to like the page and to like and share various posts.

Target Market(s)

Healthcare and potential Healthcare Staff

Industry/Entity Type

Healthcare

Colors
33b8a4
3277b5

Requirements
Must have
• Company Logo, Brand colours,
• text; "Refer a Friend and receive a £50 Bonus after just 1 completed shift"
• text; "3 easy steps to refer a friend, 1 Fill out your name on the back of your Business Card 2 Hand the card to your friend or any person you wish to refer, 3 ask your friend to present the card to us when they attend their interview"
• text; "Like and share any of our Open Days on Chatterbook for a chance to win a prize, you can find us easily by searching @CarewellStaffingPartners"
• text; "Like our Page to stay up to date with our events and offers"
Nice to have
• care worker / elderly care / support worker pictures
• Content / pics from website www.carewellstaffingpartners.co.uk

```html
<!DOCTYPE html>
<html lang="en">
<head>
<meta charset="utf-8">
<title>Refer a Friend Flyer – Carewell Staffing</title>
<link rel="stylesheet" href="https://fonts.googleapis.com/css2?family=Oswald:wght@400;500;600&family=Roboto:wght@300;400&family=Raleway:wght@300;400&display=swap">
<style>
  :root {
    --page-bg: #9aa4ab;
    --paper: #ffffff;
    --navy: #0d4f9e;
    --blue: #1a5cab;
    --brand-blue: #3277b5;
    --teal: #1ea68f;
    --brand-teal: #33b8a4;
    --ink-grey: #58595b;
    --white: #ffffff;
  }
  * { box-sizing: border-box; margin: 0; padding: 0; }
  html, body { width: 926px; height: 1200px; overflow: hidden; }
  body { background: var(--page-bg); position: relative; font-family: "Roboto", sans-serif; }

  .flyer {
    position: absolute; left: 75px; top: 48px; width: 777px; height: 1101px;
    background: var(--paper); overflow: hidden;
  }

  /* Brand block */
  .brand { position: absolute; left: 31px; top: 40px; width: 350px; height: 130px; }
  .brand-mark { position: absolute; left: 0; top: 14px; width: 56px; height: 56px; border-radius: 50%; border: 4px solid var(--navy); }
  .brand-name {
    position: absolute; left: 72px; top: 8px;
    font-family: "Roboto", sans-serif; font-weight: 400; font-size: 46px; line-height: 1.05;
    color: var(--navy); letter-spacing: -0.5px;
  }
  .brand-tagline {
    position: absolute; right: 10px; top: 112px;
    font-family: "Roboto", sans-serif; font-size: 15px; color: var(--ink-grey);
  }

  .visit-pill {
    position: absolute; left: 506px; top: 71px; width: 160px; height: 48px;
    border: 4px solid var(--navy); border-radius: 24px;
    font-family: "Oswald", sans-serif; font-size: 27px; color: var(--teal);
    display: flex; align-items: center; justify-content: center;
  }
  .web-address {
    position: absolute; left: 395px; top: 135px; width: 360px; text-align: right;
    font-family: "Roboto", sans-serif; font-size: 17px; color: var(--ink-grey);
  }

  /* Headline */
  .headline {
    position: absolute; left: 32px; top: 198px;
    font-family: "Oswald", sans-serif; font-weight: 500; font-size: 66px; line-height: 70px;
    color: var(--navy); letter-spacing: -0.5px;
  }
  .bonus-ribbon { position: absolute; left: 393px; top: 205px; width: 384px; height: 140px; }
  .bonus-text {
    position: absolute; left: 452px; top: 218px; width: 325px;
    display: flex; align-items: center; justify-content: center; gap: 12px; height: 112px;
    color: var(--white); font-family: "Oswald", sans-serif; font-weight: 600;
  }
  .bonus-amount { font-size: 82px; line-height: 1; }
  .bonus-word { font-size: 40px; line-height: 1; padding-top: 8px; }
  .subline {
    position: absolute; left: 31px; top: 344px;
    font-family: "Raleway", sans-serif; font-weight: 300; font-size: 55px; line-height: 64px;
    color: var(--ink-grey); letter-spacing: 2.4px; white-space: nowrap;
  }

  /* Steps panel */
  .steps-panel {
    position: absolute; left: 0; top: 425px; width: 777px; height: 454px;
    background: linear-gradient(90deg, var(--navy) 0%, var(--blue) 50%, #2e73bb 70%);
  }
  .care-photo {
    position: absolute; right: 0; top: 0; width: 380px; height: 454px;
    background: linear-gradient(90deg, rgba(46,115,187,0) 0%, #c9d9e6 35%, #e6ecef 70%, #9fc9b8 100%);
  }
  .steps-heading {
    position: absolute; left: 0; top: 21px; width: 445px; height: 53px;
    background: var(--teal);
    clip-path: polygon(0 0, 100% 0, 92% 100%, 0 100%);
    font-family: "Oswald", sans-serif; font-weight: 500; font-size: 28px; color: var(--white);
    padding-left: 34px; line-height: 53px;
  }
  .step-connector { position: absolute; left: 106px; top: 160px; width: 3px; height: 230px; background: var(--brand-teal); }
  .step { position: absolute; left: 0; width: 440px; height: 84px; }
  .step-number {
    position: absolute; left: 34px; top: 22px;
    font-family: "Oswald", sans-serif; font-weight: 600; font-size: 28px; color: var(--white);
  }
  .step-icon {
    position: absolute; left: 67px; top: 2px; width: 80px; height: 80px; border-radius: 50%;
    background: var(--teal); display: flex; align-items: center; justify-content: center;
  }
  .step-text {
    position: absolute; left: 168px; top: -6px; width: 262px;
    font-family: "Roboto", sans-serif; font-size: 21px; line-height: 29px; color: var(--white);
  }

  .teal-rule { position: absolute; left: 0; top: 879px; width: 777px; height: 7px; background: var(--teal); }

  /* Prize band */
  .prize-icons { position: absolute; left: 0; top: 893px; width: 777px; height: 70px; display: flex; justify-content: center; align-items: center; gap: 46px; }
  .round-icon { width: 38px; height: 38px; border-radius: 50%; background: var(--blue); display: flex; align-items: center; justify-content: center; }
  .prize-text {
    position: absolute; left: 0; top: 963px; width: 777px; text-align: center;
    font-family: "Oswald", sans-serif; font-weight: 500; font-size: 24px; color: var(--navy);
  }

  /* Footer */
  .footer { position: absolute; left: 0; top: 1010px; width: 777px; height: 91px; background: var(--teal); }
  .footer-search {
    position: absolute; left: 0; top: 0; width: 405px; height: 91px; background: var(--navy);
    clip-path: polygon(0 0, 100% 0, 91% 100%, 0 100%);
  }
  .network-dot { position: absolute; left: 30px; top: 24px; width: 44px; height: 44px; border-radius: 50%; background: var(--white); }
  .footer-search-text {
    position: absolute; left: 88px; top: 14px; width: 300px; text-align: center;
    font-family: "Oswald", sans-serif; font-size: 20px; line-height: 30px; color: var(--white);
  }
  .footer-like { position: absolute; left: 402px; top: 0; height: 91px; display: flex; align-items: center; gap: 16px; }
  .footer-like-text { font-family: "Oswald", sans-serif; font-size: 22px; color: var(--white); }
</style>
</head>
<body>
<main class="flyer">
  <header>
    <div class="brand">
      <span class="brand-mark"></span>
      <div class="brand-name">Carewell<br>Staffing</div>
      <div class="brand-tagline">Care Made Easy</div>
    </div>
    <div class="visit-pill">Visit us</div>
    <div class="web-address">www.carewellstaffingpartners.co.uk</div>
  </header>

  <section class="offer">
    <h1 class="headline">Refer a Friend<br>And receive a</h1>
    <svg class="bonus-ribbon" viewBox="0 0 384 140" aria-hidden="true">
      <defs>
        <linearGradient id="ribbonFill" x1="0" x2="1" y1="0" y2="0">
          <stop offset="0" stop-color="#1a6aa8"/>
          <stop offset="0.5" stop-color="#1e8fa0"/>
          <stop offset="1" stop-color="#1a7fa6"/>
        </linearGradient>
      </defs>
      <polygon points="0,0 384,0 384,140 0,140 70,70" fill="url(#ribbonFill)"/>
      <line x1="62" y1="13" x2="384" y2="13" stroke="#fff" stroke-width="2" stroke-dasharray="9 6"/>
      <line x1="62" y1="127" x2="384" y2="127" stroke="#fff" stroke-width="2" stroke-dasharray="9 6"/>
      <polyline points="62,13 116,70 62,127" fill="none" stroke="#fff" stroke-width="2" stroke-dasharray="9 6"/>
    </svg>
    <div class="bonus-text"><span class="bonus-amount">£50</span><span class="bonus-word">BONUS</span></div>
    <p class="subline">After just 1 completed shift</p>
  </section>

  <section class="steps-panel">
    <div class="care-photo" role="img" aria-label="Photo of a smiling care worker with an elderly woman in a wheelchair"></div>
    <h2 class="steps-heading">3 EASY STEPS TO REFER A FRIEND</h2>
    <div class="step-connector"></div>

    <div class="step" style="top:99px">
      <span class="step-number">1</span>
      <span class="step-icon">
        <svg width="38" height="42" viewBox="0 0 38 42" aria-hidden="true">
          <rect x="3" y="3" width="26" height="34" rx="2" fill="#fff"/>
          <rect x="8" y="11" width="16" height="3" fill="#1ea68f"/>
          <rect x="8" y="18" width="16" height="3" fill="#1ea68f"/>
          <rect x="8" y="25" width="10" height="3" fill="#1ea68f"/>
          <line x1="22" y1="34" x2="36" y2="14" stroke="#fff" stroke-width="5" stroke-linecap="round"/>
        </svg>
      </span>
      <p class="step-text">Fill out your name on the back of your Business Card.</p>
    </div>

    <div class="step" style="top:217px">
      <span class="step-number">2</span>
      <span class="step-icon">
        <svg width="44" height="40" viewBox="0 0 44 40" aria-hidden="true">
          <rect x="16" y="4" width="24" height="16" rx="2" fill="#fff" transform="rotate(-20 28 12)"/>
          <path d="M4 36 L16 22 L26 22 L26 27 L18 28" fill="none" stroke="#fff" stroke-width="4" stroke-linecap="round" stroke-linejoin="round"/>
        </svg>
      </span>
      <p class="step-text">Hand the card to your friend or any person you wish to refer.</p>
    </div>

    <div class="step" style="top:335px">
      <span class="step-number">3</span>
      <span class="step-icon">
        <svg width="44" height="40" viewBox="0 0 44 40" aria-hidden="true">
          <rect x="4" y="6" width="30" height="20" rx="2" fill="#fff"/>
          <rect x="4" y="11" width="30" height="4" fill="#1ea68f"/>
          <path d="M24 36 L24 24 L38 24 L38 36" fill="none" stroke="#fff" stroke-width="4" stroke-linejoin="round"/>
        </svg>
      </span>
      <p class="step-text">ask your friend to present the card to us when they attend their interview.</p>
    </div>
  </section>

  <div class="teal-rule"></div>

  <section class="prize">
    <div class="prize-icons">
      <span class="round-icon">
        <svg width="18" height="18" viewBox="0 0 18 18" aria-hidden="true"><path d="M3 9 L7 13 L15 5" fill="none" stroke="#fff" stroke-width="3" stroke-linecap="round" stroke-linejoin="round"/></svg>
      </span>
      <svg width="70" height="62" viewBox="0 0 70 62" aria-hidden="true">
        <rect x="6" y="18" width="58" height="12" fill="none" stroke="#1ea68f" stroke-width="4"/>
        <rect x="11" y="30" width="48" height="29" fill="none" stroke="#1ea68f" stroke-width="4"/>
        <line x1="35" y1="18" x2="35" y2="59" stroke="#1ea68f" stroke-width="4"/>
        <path d="M35 18 C26 4 14 8 20 16 Z M35 18 C44 4 56 8 50 16 Z" fill="none" stroke="#1ea68f" stroke-width="4"/>
      </svg>
      <span class="round-icon">
        <svg width="18" height="18" viewBox="0 0 18 18" aria-hidden="true"><path d="M3 15 C3 8 7 6 12 6 L12 2 L17 8 L12 13 L12 10 C8 10 5 11 3 15 Z" fill="#fff"/></svg>
      </span>
    </div>
    <p class="prize-text">Like and share any of our Open Days on Chatterbook for a chance to win a prize</p>
  </section>

  <footer class="footer">
    <div class="footer-search">
      <span class="network-dot"></span>
      <p class="footer-search-text">You can find us easily by searching<br>@CarewellStaffingPartners</p>
    </div>
    <div class="footer-like">
      <svg width="50" height="40" viewBox="0 0 50 40" aria-hidden="true">
        <rect x="2" y="10" width="16" height="28" rx="2" fill="none" stroke="#fff" stroke-width="3"/>
        <path d="M22 16 L30 4 C34 4 35 7 34 12 L46 12 C48 14 48 16 46 18 C48 20 48 23 45 24 C47 26 46 29 43 30 C44 33 42 35 39 35 L22 35 Z" fill="none" stroke="#fff" stroke-width="3" stroke-linejoin="round"/>
      </svg>
      <span class="footer-like-text">Like our Page to stay up to date</span>
    </div>
  </footer>
</main>
</body>
</html>
```